Flyer for the Lumen 2025 Conference

I am looking to produce a flyer for our upcoming conference, Lumen 2025. This is an annual conference that we plan to publicize on social media. The ideal designer will create a flyer that is eye-catching and effectively communicates the key information. Please see attached our logo, speaker photo, and flyer content.

Target Market(s)

All demographics

Industry/Entity Type

Christian

Font styles to use
Sans Serif

Requirements
Should not have
• Cross, church

```html
<!DOCTYPE html>
<html lang="en">
<head>
<meta charset="utf-8">
<title>Lumen 2025 Conference Flyer</title>
<link rel="stylesheet" href="https://fonts.googleapis.com/css2?family=Anton&family=Archivo+Black&family=Oswald:wght@500;600&family=Orbitron:wght@900&family=Playfair+Display:wght@900&display=swap">
<style>
  :root {
    --navy-deep: #0b1a3f;
    --navy: #0f2d7a;
    --blue: #1d44a8;
    --blue-light: #2b5ad0;
    --orange: #f47d10;
    --white: #ffffff;
    --ink: #111111;
  }
  * { margin: 0; padding: 0; box-sizing: border-box; }
  html, body { width: 861px; height: 1200px; overflow: hidden; background: var(--white); }
  .flyer {
    position: relative; width: 861px; height: 1200px; overflow: hidden;
    background: linear-gradient(160deg, var(--navy-deep) 0%, var(--navy) 35%, var(--blue) 75%, var(--navy) 100%);
    font-family: "Oswald", sans-serif; color: var(--white);
  }
  .backdrop, .photo-frame { position: absolute; left: 0; top: 0; }
  .brand {
    position: absolute; left: 538px; top: 90px;
    font-family: "Oswald", sans-serif; font-weight: 500; font-size: 60px;
    letter-spacing: 4px; line-height: 1; color: var(--white);
  }
  .title { position: absolute; left: 536px; font-family: "Anton", sans-serif; line-height: 1; }
  .title--event { top: 198px; font-size: 54px; color: var(--white); }
  .title--kind { top: 277px; font-size: 56px; color: var(--orange); }
  .title--word { top: 356px; font-size: 58px; color: var(--white); }
  .pill-label {
    position: absolute; font-family: "Playfair Display", serif; font-weight: 900;
    color: var(--ink); font-size: 40px; line-height: 1;
  }
  .pill-label--topic { left: 505px; top: 459px; }
  .pill-label--speaker { left: 390px; top: 636px; }
  .serif-block {
    position: absolute; font-family: "Playfair Display", serif; font-weight: 900;
    font-size: 38px; line-height: 1.12; color: var(--white);
  }
  .serif-block--topic { left: 468px; top: 524px; }
  .serif-block--speaker { left: 386px; top: 700px; }
  .schedule { position: absolute; left: 0; top: 832px; width: 861px; height: 130px; }
  .day { position: absolute; top: 0; }
  .day:nth-child(1) { left: 64px; }
  .day:nth-child(2) { left: 323px; }
  .day:nth-child(3) { left: 582px; }
  .day__num { font-family: "Orbitron", sans-serif; font-weight: 900; font-size: 52px; line-height: 1; color: var(--orange); letter-spacing: 2px; }
  .day__name, .day__time { font-family: "Oswald", sans-serif; font-weight: 500; font-size: 26px; line-height: 1.25; letter-spacing: -0.3px; }
  .day__name { margin-top: 2px; }
  .divider { position: absolute; top: 6px; width: 1px; height: 118px; background: rgba(255,255,255,0.5); }
  .divider--a { left: 294px; }
  .divider--b { left: 564px; }
  .venue { position: absolute; left: 70px; top: 988px; }
  .venue__pin { position: absolute; left: 0; top: 6px; }
  .venue__name { position: absolute; left: 56px; top: 0; white-space: nowrap; font-weight: 600; font-size: 35px; line-height: 1.1; color: var(--orange); }
  .venue__address { position: absolute; left: 56px; top: 46px; white-space: nowrap; font-weight: 500; font-size: 26px; line-height: 1.1; }
  .app-bar {
    position: absolute; left: 0; top: 1095px; width: 861px; height: 38px; background: var(--orange);
  }
  .app-bar__text {
    position: absolute; left: 36px; top: 8px; font-family: "Archivo Black", sans-serif;
    font-size: 17px; line-height: 1.3; color: var(--ink); letter-spacing: 0.2px; white-space: nowrap;
  }
  .store-badge { position: absolute; top: 4px; width: 84px; height: 30px; background: var(--ink); border-radius: 4px; border: 1px solid #444; }
  .store-badge--one { left: 654px; }
  .store-badge--two { left: 746px; }
  .contacts { position: absolute; left: 28px; top: 1148px; display: flex; align-items: center; gap: 8px; white-space: nowrap; }
  .contact { display: flex; align-items: center; gap: 6px; font-family: "Archivo Black", sans-serif; font-size: 21px; line-height: 1; }
  .contact__icon { width: 24px; height: 24px; background: var(--orange); border-radius: 4px; display: flex; align-items: center; justify-content: center; }
</style>
</head>
<body>
<main class="flyer">
  <svg class="backdrop" width="861" height="1200" viewBox="0 0 861 1200" aria-hidden="true">
    <polygon points="300,1200 861,560 861,700 420,1200" fill="#2a58c8" opacity="0.35"/>
    <polygon points="120,1200 861,830 861,900 260,1200" fill="#3a68d8" opacity="0.25"/>
    <polygon points="861,240 861,420 600,760" fill="#2450c0" opacity="0.3"/>
    <polygon points="0,760 140,1200 60,1200 0,980" fill="#2a58c8" opacity="0.25"/>
    <polygon points="400,0 560,0 420,300" fill="#1a3a8c" opacity="0.4"/>
  </svg>

  <svg class="photo-frame" width="861" height="760" viewBox="0 0 861 760">
    <defs>
      <linearGradient id="portraitTone" x1="0" y1="0" x2="1" y2="1">
        <stop offset="0" stop-color="#0c1630"/>
        <stop offset="0.5" stop-color="#1f55c4"/>
        <stop offset="1" stop-color="#10204a"/>
      </linearGradient>
    </defs>
    <polygon role="img" aria-label="Portrait of the speaker in a bright blue suit and glasses"
      points="0,45 330,45 377,151 513,372 352,686 295,724 0,730" fill="url(#portraitTone)"/>
    <polyline points="377,151 513,372 352,686 295,724 0,730" fill="none" stroke="#f47d10" stroke-width="6" stroke-linejoin="round"/>
    <path d="M 488,453 L 788,453 A 28,28 0 0 1 788,510 L 458,510 Z" fill="#f47d10"/>
    <path d="M 400,629 L 682,629 A 28,28 0 0 1 682,686 L 370,686 Z" fill="#f47d10"/>
  </svg>

  <div class="brand">KAVORA</div>

  <h1 class="title title--event">LUMEN 2025</h1>
  <p class="title title--kind">A PROPHETIC</p>
  <p class="title title--word">CONFERENCE</p>

  <p class="pill-label pill-label--topic">TOPIC:</p>
  <p class="serif-block serif-block--topic">THE VOICE OF<br>THE LORD</p>

  <p class="pill-label pill-label--speaker">SPEAKER:</p>
  <p class="serif-block serif-block--speaker">PROPHET<br>ELIAS MAREN</p>

  <section class="schedule">
    <div class="day">
      <div class="day__num">26</div>
      <div class="day__name">Friday, December</div>
      <div class="day__time">6:30PM - 9:00PM</div>
    </div>
    <div class="day">
      <div class="day__num">27</div>
      <div class="day__name">Saturday, December</div>
      <div class="day__time">5:30PM - 8:00PM</div>
    </div>
    <div class="day">
      <div class="day__num">28</div>
      <div class="day__name">Sunday, December</div>
      <div class="day__time">4:30PM - 7:00PM</div>
    </div>
    <span class="divider divider--a"></span>
    <span class="divider divider--b"></span>
  </section>

  <section class="venue">
    <svg class="venue__pin" width="42" height="42" viewBox="0 0 42 42" aria-hidden="true">
      <circle cx="21" cy="21" r="20" fill="#f47d10"/>
      <path d="M21 9 C15 9 12 13 12 17.5 C12 24 21 33 21 33 C21 33 30 24 30 17.5 C30 13 27 9 21 9 Z" fill="#fff"/>
      <circle cx="21" cy="17.5" r="3.5" fill="#f47d10"/>
    </svg>
    <p class="venue__name">The Harborview Performing Arts Center</p>
    <p class="venue__address">218 Alder Grove Street, Eastfield, Maine 04120</p>
  </section>

  <section class="app-bar">
    <p class="app-bar__text">Download the KAVORA App to stay updated on the event</p>
    <span class="store-badge store-badge--one"></span>
    <span class="store-badge store-badge--two"></span>
  </section>

  <footer class="contacts">
    <span class="contact">
      <span class="contact__icon">
        <svg width="16" height="16" viewBox="0 0 24 24" aria-hidden="true"><path d="M6.6 10.8a15 15 0 0 0 6.6 6.6l2.2-2.2c.3-.3.7-.4 1-.2 1.1.4 2.3.6 3.6.6.6 0 1 .4 1 1V20c0 .6-.4 1-1 1A17 17 0 0 1 3 4c0-.6.4-1 1-1h3.5c.6 0 1 .4 1 1 0 1.3.2 2.5.6 3.6.1.3 0 .7-.2 1z" fill="#fff"/></svg>
      </span>207 555 0148
    </span>
    <span class="contact">
      <span class="contact__icon">
        <svg width="16" height="16" viewBox="0 0 24 24" aria-hidden="true"><rect x="3" y="6" width="18" height="12" rx="1.5" fill="none" stroke="#fff" stroke-width="2"/><path d="M3 7l9 6 9-6" fill="none" stroke="#fff" stroke-width="2"/></svg>
      </span>contact@kavora.org
    </span>
    <span class="contact">
      <span class="contact__icon">
        <svg width="16" height="16" viewBox="0 0 24 24" aria-hidden="true"><circle cx="12" cy="12" r="9" fill="none" stroke="#fff" stroke-width="2"/><path d="M3 12h18M12 3c3 3 3 15 0 18M12 3c-3 3-3 15 0 18" fill="none" stroke="#fff" stroke-width="1.6"/></svg>
      </span>www.kavora.org
    </span>
  </footer>
</main>
</body>
</html>
```